Stationery design for software development / consultancy company

We need stationary design based on company logo.

We are based in London, UK and we are providing integration solutions development / consultancy services for KVT integration projects across UK.

Our name refers two words - integration and grace - and it shows our clients our main specialization field and key characteristics of our solutions / products. We also would like to be associated with follow words: smart, reliable, unique.

Project delivery should include:
- Powerpoint template (needs to have a Cover Page, Table of Contents, 1-2 sample pages, and a Closing/Summary slide at the end)
- Letterhead A4 (Word template)
- Standard invoice A4 (Word template)
- With Compliments Slips A5 (Word template)
- Business card (adobe illustrator)

Attached is logo in vector (please use logo with white background!) and company details for printed stationery.

highly skilled IT professionals

Software

• Clear background in all A4/A5 documents.
All text should be editable, i.e. I will need sources.
• I would prefer light, web 2.0 style colours, follow are in my main interest:
- combination of light grey and orange
- Logo colours
• Please no watermarks on printed stationary

```html
<!DOCTYPE html>
<html lang="en">
<head>
<meta charset="utf-8">
<title>Nexalink Invoice</title>
<link href="https://fonts.googleapis.com/css2?family=Arimo:ital,wght@0,400;0,700;1,400&family=Tinos:wght@400;700&display=swap" rel="stylesheet">
<style>
  :root {
    --backdrop: #2b2b2b;
    --paper: #ffffff;
    --ink: #111111;
    --muted: #c8c8c8;
    --rule: #d0d0d0;
    --brand: #1f8fc4;
    --band: #dcdcdc;
    --edge: #8c7a58;
  }
  * { box-sizing: border-box; margin: 0; padding: 0; }
  html, body { width: 1200px; height: 844px; overflow: hidden; }
  body { background: var(--backdrop); position: relative; font-family: "Arimo", Arial, sans-serif; color: var(--ink); }

  .invoice-page {
    position: absolute; left: 313px; top: 28px; width: 600px; height: 782px;
    background: var(--paper); border-right: 3px solid var(--edge);
  }
  .brand { position: absolute; left: 52px; top: 34px; display: flex; align-items: center; gap: 8px; }
  .brand-dot { width: 24px; height: 24px; border-radius: 50%; background: var(--brand); }
  .brand-name { font-size: 28px; font-weight: 700; color: #555; letter-spacing: -0.5px; }

  .company-address {
    position: absolute; left: 58px; top: 79px; width: 170px;
    font-family: "Tinos", "Times New Roman", serif; font-size: 8.5px; line-height: 10.5px; text-align: center;
  }
  .doc-title { position: absolute; left: 437px; top: 27px; font-size: 24px; font-weight: 700; color: var(--muted); }
  .meta-field { position: absolute; font-size: 12px; }
  .meta-number { left: 366px; top: 83px; }
  .meta-date { left: 381px; top: 112px; }
  .header-rule { position: absolute; left: 30px; top: 140px; width: 540px; height: 3px; background: var(--rule); }

  .party { position: absolute; top: 155px; font-family: "Tinos", "Times New Roman", serif; font-size: 11.5px; }
  .party-label { position: absolute; top: 0; font-family: "Arimo", Arial, sans-serif; font-weight: 700; font-size: 11px; white-space: nowrap; }
  .party-line { position: absolute; white-space: nowrap; }
  .bill-to { left: 45px; }
  .ship-to { left: 381px; }

  table { position: absolute; border-collapse: collapse; table-layout: fixed; }
  th, td { border: 1.5px solid var(--ink); font-size: 10px; font-weight: 700; text-align: center; }
  th { height: 21px; }
  .order-table { left: 30px; top: 259px; width: 540px; }
  .order-table td { height: 27px; }
  .lines-table { left: 30px; top: 321px; width: 540px; }
  .lines-table td { height: 177px; }

  .totals-table { left: 420px; top: 519px; width: 150px; }
  .totals-table th { height: 27.4px; font-size: 9px; text-align: right; padding-right: 4px; line-height: 9px; }
  .totals-table td { font-weight: 400; }

  .notes-label { position: absolute; left: 52px; top: 544px; font-size: 11px; font-weight: 700; }
  .notes-box { position: absolute; left: 43px; top: 566px; width: 251px; height: 128px; border: 2px dashed #333; }
  .thanks-band {
    position: absolute; left: 45px; top: 710px; width: 341px; height: 27px; background: var(--band);
    font-size: 12px; font-style: italic; text-align: center; line-height: 27px; color: #333;
  }
</style>
</head>
<body>
  <main class="invoice-page">
    <div class="brand"><span class="brand-dot"></span><span class="brand-name">Nexalink</span></div>
    <div class="company-address">
      Nexalink Limited, 42 Ash Court<br>
      18 Harbour Lane, London<br>
      EC9 4ZZ, United Kingdom<br>
      Tel: +44(0)20 000 4417
    </div>

    <h1 class="doc-title">INVOICE</h1>
    <div class="meta-field meta-number">Invoice No. :</div>
    <div class="meta-field meta-date">Date :</div>
    <div class="header-rule"></div>

    <section class="party bill-to">
      <span class="party-label">Bill To :</span>
      <span class="party-line" style="left:69px;top:0">Name :</span>
      <span class="party-line" style="left:69px;top:23px">Address1 :</span>
      <span class="party-line" style="left:69px;top:47px">Address2:</span>
      <span class="party-line" style="left:69px;top:70px">Mobile :</span>
    </section>
    <section class="party ship-to">
      <span class="party-label">Ship To :</span>
      <span class="party-line" style="left:0;top:24px">SH Name :</span>
      <span class="party-line" style="left:0;top:48px">SHAddress1 :</span>
      <span class="party-line" style="left:0;top:71px">Mobile</span>
    </section>

    <table class="order-table">
      <colgroup><col style="width:73px"><col style="width:111px"><col style="width:86px"><col style="width:75px"><col style="width:99px"><col style="width:96px"></colgroup>
      <tr><th>P.O#</th><th>Sales Rep. Name</th><th>Ship Date</th><th>Ship Via</th><th>Terms</th><th>Due Date</th></tr>
      <tr><td></td><td></td><td></td><td></td><td></td><td></td></tr>
    </table>

    <table class="lines-table">
      <colgroup><col style="width:73px"><col style="width:238px"><col style="width:77px"><col style="width:73px"><col style="width:79px"></colgroup>
      <tr><th>Product ID</th><th>Description</th><th>Unit Price</th><th>Quantity</th><th>Line Total</th></tr>
      <tr><td></td><td></td><td></td><td></td><td></td></tr>
    </table>

    <table class="totals-table">
      <colgroup><col style="width:71px"><col style="width:79px"></colgroup>
      <tr><th>Subtotal</th><td></td></tr>
      <tr><th>PST</th><td></td></tr>
      <tr><th>GST</th><td></td></tr>
      <tr><th>Shipping &amp;<br>Handling</th><td></td></tr>
      <tr><th>Total</th><td></td></tr>
      <tr><th>Paid</th><td></td></tr>
      <tr><th>Total Due</th><td></td></tr>
    </table>

    <div class="notes-label">Notes</div>
    <div class="notes-box"></div>
    <div class="thanks-band">THANK YOU FOR YOUR BUSINESS</div>
  </main>
</body>
</html>
```